Business Card Design Project

Business Card
We are rebranding with a new logo
Industry/Entity Type
Business
Contact Information for Business Card
Dennis Morvale +61 487215963 dennis@quorv.com.au P.O. Box 872 Fernlow QLD 4309
Requirements
Must have
- Logo

```html
<!DOCTYPE html>
<html lang="en">
<head>
<meta charset="utf-8">
<title>Quorv International – Business Card</title>
<link href="https://fonts.googleapis.com/css2?family=Questrial&display=swap" rel="stylesheet">
<style>
  :root {
    --backdrop: #3b3b3b;
    --card-white: #ffffff;
    --card-mist: #ededed;
    --blue-light: #2a90c2;
    --blue-mid: #16658f;
    --blue-deep: #053e5b;
    --ink-dark: #1c1c1c;
    --text-light: #ffffff;
    --text-soft: #e3eef4;
  }
  html, body {
    margin: 0;
    padding: 0;
    width: 1200px;
    height: 965px;
    overflow: hidden;
    background: var(--backdrop);
  }
  .canvas {
    position: relative;
    width: 1200px;
    height: 965px;
  }
  .business-card {
    position: absolute;
    left: 50px;
    top: 169px;
    width: 978px;
    height: 557px;
    transform: scale(1.1247);
    transform-origin: 0 0;
    border-radius: 46px;
    overflow: hidden;
    background: radial-gradient(ellipse at 55% 20%, var(--card-white) 0%, var(--card-mist) 100%);
    box-shadow: 0 10px 30px rgba(0,0,0,0.45);
    font-family: "Questrial", "Century Gothic", sans-serif;
  }
  .lower-band {
    position: absolute;
    inset: 0;
    background: linear-gradient(90deg, var(--blue-light) 0%, var(--blue-mid) 55%, var(--blue-deep) 100%);
    clip-path: polygon(0 395px, 978px 170px, 978px 557px, 0 557px);
  }
  .brand-name {
    position: absolute;
    left: 44px;
    top: 246px;
    margin: 0;
    font-size: 27px;
    font-weight: 400;
    letter-spacing: 3px;
    color: var(--ink-dark);
  }
  .holder-name {
    position: absolute;
    right: 53px;
    top: 370px;
    margin: 0;
    font-size: 29px;
    font-weight: 400;
    color: var(--text-light);
    letter-spacing: 0.5px;
  }
  .contact-list {
    position: absolute;
    right: 53px;
    top: 437px;
    margin: 0;
    padding: 0;
    list-style: none;
    text-align: right;
  }
  .contact-list li {
    display: flex;
    justify-content: flex-end;
    align-items: center;
    gap: 12px;
    height: 28px;
    font-size: 21px;
    color: var(--text-soft);
  }
  .contact-icon {
    width: 22px;
    height: 22px;
    flex: none;
  }
  .postal-address {
    position: absolute;
    left: 42px;
    top: 468px;
    margin: 0;
    font-style: normal;
    font-size: 21px;
    line-height: 28px;
    color: var(--text-soft);
  }
</style>
</head>
<body>
<div class="canvas">
  <div class="business-card">
    <div class="lower-band" role="img" aria-label="Decorative blue and orange wave band across the lower card"></div>

    <h1 class="brand-name">QUORV INTERNATIONAL</h1>

    <h2 class="holder-name">DENNIS MORVALE</h2>

    <ul class="contact-list">
      <li>+61 487215963
        <svg class="contact-icon" viewBox="0 0 24 24" aria-hidden="true"><path fill="#fff" d="M6.6 2.5c.6-.4 1.4-.2 1.8.4l2 3.1c.4.6.2 1.3-.3 1.7l-1.4 1c.8 2 2.6 3.9 4.6 4.8l1-1.4c.4-.6 1.2-.7 1.7-.3l3.1 2c.6.4.8 1.2.4 1.8l-1 1.7c-.7 1.1-2 1.6-3.2 1.2C9.8 16.6 6.4 13.2 4.5 7.7c-.4-1.2.1-2.5 1.2-3.2z"/></svg>
      </li>
      <li>dennis@quorv.com.au
        <svg class="contact-icon" viewBox="0 0 24 24" aria-hidden="true"><rect x="2" y="5" width="20" height="14" fill="#fff"/><path d="M2.5 5.5 12 13l9.5-7.5M2.5 18.5 9 12m12.5 6.5L15 12" stroke="#0b4d70" stroke-width="1.6" fill="none"/></svg>
      </li>
      <li>www.quorv.com.au
        <svg class="contact-icon" viewBox="0 0 24 24" aria-hidden="true"><g fill="none" stroke="#fff" stroke-width="1.6"><circle cx="12" cy="12" r="9.5"/><ellipse cx="12" cy="12" rx="4" ry="9.5"/><path d="M2.5 12h19M4 7h16M4 17h16"/></g></svg>
      </li>
    </ul>

    <address class="postal-address">P.O. Box 872 Fernlow<br>QLD 4309</address>
  </div>
</div>
</body>
</html>
```